Custom Mexican Train Dominos Scorecard

My wife and I regularly play Mexican Train dominos with our friends and family and would like to create a series of custom scorecards specific to our various groups that we play with. The idea would be to have them printed on pads or in notebooks that over time will hold a record of all of our games. Searching around on the web, the only "off the shelf" that I see are pretty plain and boring (see attached). We would love something with a fun and playful mid-century graphic feel to it. Can be a single color or more than one. We want to have the player names incorporated into the design, so for the first one the names would be Olive, Walter, Ruby & Oscar. We will want a place to date each card and of course boxes to fill out the score. I have included a few examples of how the scorecard is basically laid out. Can be any size and can be done in landscape or portrait. I think I would just like the title to say "Domino Night" or potentially no title at all with just a fun domino graphic. Thank you!

Requirements
Must have
• Basic score layout
Nice to have
• nothing in particular
Should not have
• nothing in particular

```html
<!DOCTYPE html>
<html lang="en">
<head>
<meta charset="utf-8">
<title>Domino Night Scorecard</title>
<link href="https://fonts.googleapis.com/css2?family=Rye&family=Quicksand:wght@400;500&display=swap" rel="stylesheet">
<style>
:root{
  --maroon:#2e1018;
  --maroon-soft:#4a2530;
  --ink:#111315;
  --pink:#f4c9dc;
  --blush:#fbf5f9;
  --gold:#c8a64a;
  --gold-dark:#a98a33;
  --tile:#f6f8f7;
  --cream:#fbf1f4;
  --line:#6b6b6b;
}
*{box-sizing:border-box;margin:0;padding:0}
html,body{width:856px;height:1200px;overflow:hidden;background:#fff}
.card{position:absolute;left:13px;top:12px;width:830px;height:1174px;background:var(--maroon);border:1px solid #555}
.masthead{position:absolute;left:0;top:0;width:830px;height:194px}
.flourish{position:absolute;border-radius:50%;background:radial-gradient(ellipse at center,rgba(244,201,220,.35),rgba(244,201,220,0) 70%)}
.flourish--top{left:218px;top:2px;width:380px;height:92px}
.flourish--bottom{left:350px;top:130px;width:116px;height:60px}
.title{position:absolute;left:0;width:830px;top:92px;text-align:center;font-family:"Rye",serif;font-size:31px;color:var(--cream);letter-spacing:.5px}
.rule{position:absolute;left:258px;top:138px;width:300px;height:1px;background:var(--pink);opacity:.8}
.train{position:absolute;left:639px;top:31px;width:171px;height:107px;background:linear-gradient(#2a0e14,#1f0a0f);border-radius:6px;opacity:.9}
.sheet{position:absolute;left:0;top:194px;width:830px;display:grid;
  grid-template-columns:253px 80px 80px 80px 77px 68px 71px 67px 54px;
  grid-template-rows:67px 59px 56px 55px 61px 56px 49px 49px 56px 56px 55px 56px 55px 54px 65px 74px 57px}
.label{background:var(--maroon);display:flex;align-items:center;justify-content:center;gap:22px}
.label--band{background:var(--ink);color:var(--pink);font-family:"Quicksand",sans-serif;font-size:21px;font-weight:400}
.label--sub{background:linear-gradient(var(--maroon) 0 13px,var(--ink) 13px)}
.label--sub span{margin-top:13px}
.cell{background:#fff;border-left:1px solid var(--line);border-bottom:1px solid #9a9a9a}
.cell--name{background:var(--blush);font-family:"Rye",serif;font-size:14px;color:#111;display:flex;align-items:center;justify-content:center}
.cell--total{background:var(--blush);border-top:3px double #111}
.date-row{grid-column:2 / span 8;background:#fff;border-left:1px solid var(--line);position:relative;font-family:"Quicksand",sans-serif;font-size:17px;color:#222}
.date-row span{position:absolute;right:8px;bottom:6px}
.domino{width:101px;height:41px;border-radius:21px;background:var(--gold);box-shadow:inset 0 -2px 0 var(--gold-dark);display:flex;align-items:center;justify-content:center}
.tile{width:70px;height:31px;background:var(--tile);border-radius:5px;display:flex;position:relative}
.tile::after{content:"";position:absolute;left:34.5px;top:4px;width:1.3px;height:23px;background:#111}
.half{flex:1;display:grid;grid-template-rows:repeat(3,1fr);grid-auto-flow:column;align-items:center;justify-items:center;padding:3px 4px}
.half i{width:4px;height:4px;border-radius:50%;background:#111}
.half--one{grid-template-rows:1fr}
.value{width:40px;text-align:center;font-family:"Rye",serif;font-size:27px;color:var(--cream)}
</style>
</head>
<body>
<div class="card">
  <header class="masthead">
    <div class="flourish flourish--top" role="img" aria-label="Decorative scroll ornament above the title"></div>
    <div class="flourish flourish--bottom" role="img" aria-label="Decorative scroll ornament below the title"></div>
    <h1 class="title">Domino Night</h1>
    <div class="rule"></div>
    <div class="train" role="img" aria-label="Faint steam locomotive illustration"></div>
  </header>

  <div class="sheet">
    <div class="label label--band">Player’s Name</div>
    <div class="cell cell--name">Olive</div><div class="cell cell--name">Walter</div><div class="cell cell--name">Ruby</div><div class="cell cell--name">Oscar</div><div class="cell cell--name"></div><div class="cell cell--name"></div><div class="cell cell--name"></div><div class="cell cell--name"></div>

    <div class="label"><div class="domino"><div class="tile"><div class="half"><i></i><i></i><i></i><i></i><i></i><i></i><i></i><i></i><i></i><i></i><i></i><i></i></div><div class="half"><i></i><i></i><i></i><i></i><i></i><i></i><i></i><i></i><i></i><i></i><i></i><i></i></div></div></div><span class="value">12</span></div>
    <div class="cell"></div><div class="cell"></div><div class="cell"></div><div class="cell"></div><div class="cell"></div><div class="cell"></div><div class="cell"></div><div class="cell"></div>

    <div class="label"><div class="domino"><div class="tile"><div class="half"><i></i><i></i><i></i><i></i><i></i><i></i><i></i><i></i><i></i><i></i><i></i></div><div class="half"><i></i><i></i><i></i><i></i><i></i><i></i><i></i><i></i><i></i><i></i><i></i></div></div></div><span class="value">11</span></div>
    <div class="cell"></div><div class="cell"></div><div class="cell"></div><div class="cell"></div><div class="cell"></div><div class="cell"></div><div class="cell"></div><div class="cell"></div>

    <div class="label"><div class="domino"><div class="tile"><div class="half"><i></i><i></i><i></i><i></i><i></i><i></i><i></i><i></i><i></i><i></i></div><div class="half"><i></i><i></i><i></i><i></i><i></i><i></i><i></i><i></i><i></i><i></i></div></div></div><span class="value">10</span></div>
    <div class="cell"></div><div class="cell"></div><div class="cell"></div><div class="cell"></div><div class="cell"></div><div class="cell"></div><div class="cell"></div><div class="cell"></div>

    <div class="label"><div class="domino"><div class="tile"><div class="half"><i></i><i></i><i></i><i></i><i></i><i></i><i></i><i></i><i></i></div><div class="half"><i></i><i></i><i></i><i></i><i></i><i></i><i></i><i></i><i></i></div></div></div><span class="value">9</span></div>
    <div class="cell"></div><div class="cell"></div><div class="cell"></div><div class="cell"></div><div class="cell"></div><div class="cell"></div><div class="cell"></div><div class="cell"></div>

    <div class="label"><div class="domino"><div class="tile"><div class="half"><i></i><i></i><i></i><i></i><i></i><i></i><i></i><i></i></div><div class="half"><i></i><i></i><i></i><i></i><i></i><i></i><i></i><i></i></div></div></div><span class="value">8</span></div>
    <div class="cell"></div><div class="cell"></div><div class="cell"></div><div class="cell"></div><div class="cell"></div><div class="cell"></div><div class="cell"></div><div class="cell"></div>

    <div class="label"><div class="domino"><div class="tile"><div class="half"><i></i><i></i><i></i><i></i><i></i><i></i><i></i></div><div class="half"><i></i><i></i><i></i><i></i><i></i><i></i><i></i></div></div></div><span class="value">7</span></div>
    <div class="cell"></div><div class="cell"></div><div class="cell"></div><div class="cell"></div><div class="cell"></div><div class="cell"></div><div class="cell"></div><div class="cell"></div>

    <div class="label label--band label--sub"><span>Sub Total</span></div>
    <div class="cell"></div><div class="cell"></div><div class="cell"></div><div class="cell"></div><div class="cell"></div><div class="cell"></div><div class="cell"></div><div class="cell"></div>

    <div class="label"><div class="domino"><div class="tile"><div class="half"><i></i><i></i><i></i><i></i><i></i><i></i></div><div class="half"><i></i><i></i><i></i><i></i><i></i><i></i></div></div></div><span class="value">6</span></div>
    <div class="cell"></div><div class="cell"></div><div class="cell"></div><div class="cell"></div><div class="cell"></div><div class="cell"></div><div class="cell"></div><div class="cell"></div>

    <div class="label"><div class="domino"><div class="tile"><div class="half"><i></i><i></i><i></i><i></i><i></i></div><div class="half"><i></i><i></i><i></i><i></i><i></i></div></div></div><span class="value">5</span></div>
    <div class="cell"></div><div class="cell"></div><div class="cell"></div><div class="cell"></div><div class="cell"></div><div class="cell"></div><div class="cell"></div><div class="cell"></div>

    <div class="label"><div class="domino"><div class="tile"><div class="half"><i></i><i></i><i></i><i></i></div><div class="half"><i></i><i></i><i></i><i></i></div></div></div><span class="value">4</span></div>
    <div class="cell"></div><div class="cell"></div><div class="cell"></div><div class="cell"></div><div class="cell"></div><div class="cell"></div><div class="cell"></div><div class="cell"></div>

    <div class="label"><div class="domino"><div class="tile"><div class="half"><i></i><i></i><i></i></div><div class="half"><i></i><i></i><i></i></div></div></div><span class="value">3</span></div>
    <div class="cell"></div><div class="cell"></div><div class="cell"></div><div class="cell"></div><div class="cell"></div><div class="cell"></div><div class="cell"></div><div class="cell"></div>

    <div class="label"><div class="domino"><div class="tile"><div class="half"><i></i><i></i></div><div class="half"><i></i><i></i></div></div></div><span class="value">2</span></div>
    <div class="cell"></div><div class="cell"></div><div class="cell"></div><div class="cell"></div><div class="cell"></div><div class="cell"></div><div class="cell"></div><div class="cell"></div>

    <div class="label"><div class="domino"><div class="tile"><div class="half half--one"><i></i></div><div class="half half--one"><i></i></div></div></div><span class="value">1</span></div>
    <div class="cell"></div><div class="cell"></div><div class="cell"></div><div class="cell"></div><div class="cell"></div><div class="cell"></div><div class="cell"></div><div class="cell"></div>

    <div class="label"><div class="domino"><div class="tile"><div class="half"></div><div class="half"></div></div></div><span class="value">0</span></div>
    <div class="cell"></div><div class="cell"></div><div class="cell"></div><div class="cell"></div><div class="cell"></div><div class="cell"></div><div class="cell"></div><div class="cell"></div>

    <div class="label label--band">Game Total</div>
    <div class="cell cell--total"></div><div class="cell cell--total"></div><div class="cell cell--total"></div><div class="cell cell--total"></div><div class="cell cell--total"></div><div class="cell cell--total"></div><div class="cell cell--total"></div><div class="cell cell--total"></div>

    <div class="label"></div>
    <div class="date-row"><span>Date: ..............................................</span></div>
  </div>
</div>
</body>
</html>
```